Bright Path Notes Wordpress Blog

I need to design a WordPress blog page. The name of the Blog is "Bright Path Notes". I am hoping for a simple design that is easy for me to post future posts to. I like the color teal for this. The website is brightpathnotesblog.com where I am going to write a personal blog. I don't have a logo for this, but am hoping for a header that has some swirly, but classy looking text. Easy on the eyes. The website will only have a couple of pages - the home landing page, and an about me page.

Font styles to use
Script

Colors
00a990
86cfc6
cfeae6

Requirements
Must have
• A header for the landing page of the blog. Clean layout of where the blog posts will lie.

```html
<!DOCTYPE html>
<html lang="en">
<head>
<meta charset="utf-8">
<title>Bright Path Notes</title>
<link href="https://fonts.googleapis.com/css2?family=Roboto+Condensed:wght@400;700&family=Open+Sans:ital,wght@0,400;0,600;1,400&display=swap" rel="stylesheet">
<style>
:root{
  --teal:#66bdb8;
  --teal-deep:#00a990;
  --teal-soft:#86cfc6;
  --teal-pale:#cfeae6;
  --gold:#e9c43a;
  --ink:#3b3b3b;
  --body:#6f6f6f;
  --muted:#8d8d8d;
  --line:#e6e6e6;
  --card:#fafafa;
  --footer:#2b2b2b;
  --star:#f0b429;
}
*{box-sizing:border-box;margin:0;padding:0}
html,body{width:1200px;height:2338px;overflow:hidden;background:#fff}
body{position:relative;font-family:"Open Sans",Arial,sans-serif;color:var(--body)}
.abs{position:absolute}

/* hero */
.hero{left:0;top:0;width:1200px;height:600px;overflow:hidden}
.hero-photo{left:0;top:0;width:1200px;height:545px;
  background:linear-gradient(100deg,#8fa35a 0%,#c9b28f 14%,#d9c2ad 30%,#c7c9c2 45%,#dfe3e2 65%,#eef0ef 100%)}
.hero-swoosh{left:0;top:545px;width:1200px;height:36px;
  background:linear-gradient(90deg,var(--gold) 0%,#d9d08a 35%,var(--teal-soft) 65%,var(--teal) 100%)}
.brand{left:97px;top:46px;font-family:"Roboto Condensed",Arial,sans-serif;font-weight:700;font-size:31px;line-height:36px;color:#fff;letter-spacing:.3px}
.nav{left:668px;top:53px;display:flex;gap:30px;font-family:"Roboto Condensed",Arial,sans-serif;font-size:13px;color:#2f2f2f;text-transform:uppercase}
.search{left:941px;top:45px;width:157px;height:30px;background:#fff;border-radius:15px;font-size:10px;color:#999;padding:8px 14px}
.search svg{position:absolute;right:12px;top:10px}
.hero-copy{left:756px;top:226px;width:370px}
.hero-copy h1{font-family:"Roboto Condensed",Arial,sans-serif;font-weight:700;font-size:40px;color:var(--ink);line-height:48px}
.hero-copy p{margin-top:10px;font-size:12px;line-height:21px;color:#555}
.btn{display:inline-flex;align-items:center;gap:6px;margin-top:20px;height:34px;padding:0 13px;background:var(--teal);color:#fff;font-family:"Roboto Condensed",Arial,sans-serif;font-size:13px;border-radius:3px;text-transform:uppercase;box-shadow:0 2px 0 #4a9a95}
.dots{left:756px;top:422px;display:flex;gap:7px;align-items:center}
.dots i{display:block;width:11px;height:11px;border-radius:50%;background:#4a4a4a}
.dots i.on{width:17px;height:17px;background:var(--teal);border:3px solid #fff;box-shadow:0 0 0 1px var(--teal)}

/* posts */
.post{left:98px;width:689px;height:256px;border:1px solid var(--line);background:var(--card)}
.post .pic{position:absolute;left:0;top:0;width:304px;height:254px}
.post .pic::after{content:"";position:absolute;left:12px;top:12px;right:12px;bottom:12px;border:1px solid rgba(255,255,255,.7)}
.post .txt{position:absolute;left:335px;top:14px;width:335px}
.post h2{font-weight:400;font-size:15.5px;line-height:24px;color:var(--ink);padding-bottom:12px;border-bottom:1px solid #eee}
.meta{display:flex;gap:28px;margin-top:14px;font-size:10.5px;font-style:italic;color:var(--muted)}
.meta span{display:flex;align-items:center;gap:6px}
.excerpt{margin-top:12px;font-size:11px;line-height:20px;color:#777}
.share{display:flex;align-items:center;gap:9px;margin-top:12px;font-size:15px;color:var(--teal)}
.share i{display:block;width:11px;height:11px;border-radius:50%;background:#444}
.share-btns{display:flex;gap:8px;margin-top:14px}
.share-btns span{display:flex;align-items:center;gap:4px;font-size:9px;color:#444}
.share-btns b{font-weight:400;background:#4b6fa5;color:#fff;padding:2px 6px;border-radius:2px}
.share-btns em{font-style:normal;border:1px solid #ccc;padding:1px 4px;border-radius:2px}

/* sidebar */
.profile{left:837px;top:659px;width:263px;height:299px;border:1px solid var(--line);background:var(--card)}
.profile .band{position:absolute;left:0;top:0;width:261px;height:73px;background:var(--teal)}
.avatar{position:absolute;left:73px;top:21px;width:114px;height:114px;border-radius:50%;border:3px solid #fff;background:linear-gradient(160deg,#c8cdd6,#6c7486)}
.profile h3{position:absolute;top:150px;width:100%;text-align:center;font-family:"Roboto Condensed",Arial,sans-serif;font-weight:400;font-size:15px;color:var(--ink)}
.profile p{position:absolute;top:180px;left:10px;right:10px;text-align:center;font-size:10.5px;font-style:italic;line-height:20px;color:#666}
.stars{color:var(--star);font-size:11px;letter-spacing:1px}
.stars s{text-decoration:none;color:#cfcfcf}
.profile .stars{position:absolute;top:267px;width:100%;text-align:center}
.side-title{left:835px;top:993px;font-family:"Roboto Condensed",Arial,sans-serif;font-size:21px;color:#444}
.review{left:837px;width:263px;height:131px;border-bottom:1px solid #eee}
.review .pic{position:absolute;left:0;top:0;width:100px;height:106px}
.review .body{position:absolute;left:115px;top:0;width:150px}
.review h4{font-weight:400;font-size:12.5px;color:#555}
.review .stars{margin-top:3px}
.review p{margin-top:4px;font-size:10.5px;line-height:17px;color:#666}
.review .by{margin-top:9px;display:flex;align-items:center;gap:8px;font-size:10px;color:#666}
.promo{left:837px;top:1505px;width:263px;height:257px;border:1px solid #d9c48a;background:linear-gradient(170deg,#b7bdc1,#7b848b 60%,#555c62)}

/* pagination */
.pager{left:98px;top:1824px;display:flex;align-items:center;gap:9px;font-size:12px;color:#333}
.pager span{display:flex;align-items:center;justify-content:center;width:26px;height:26px;border:1px solid #555;background:#fff}
.pager span.on{background:var(--teal);border-color:var(--teal);color:#fff}

/* photo strip */
.strip{left:0;top:1934px;width:1200px;height:208px;display:flex}
.strip div{height:208px}
.follow{left:514px;top:2014px;width:173px;height:38px;background:#fff;display:flex;align-items:center;justify-content:center;gap:8px;font-family:"Roboto Condensed",Arial,sans-serif;font-size:13px;color:#333;border-radius:2px}
.follow i{display:block;width:11px;height:11px;border-radius:2px;background:#333}

/* footer */
.footer{left:0;top:2142px;width:1200px;height:196px;background:var(--footer);color:#fff}
.f-icons{position:absolute;top:49px;left:0;width:100%;display:flex;justify-content:center;gap:11px}
.f-icons i{display:block;width:24px;height:24px;border-radius:4px;background:#fff}
.f-nav{position:absolute;top:90px;width:100%;text-align:center;font-size:13px;word-spacing:2px}
.f-copy{position:absolute;top:121px;width:100%;text-align:center;font-size:13px}
</style>
</head>
<body>

<header class="abs hero">
  <div class="abs hero-photo" role="img" aria-label="Smiling woman in a leather jacket resting her chin on her hand, soft sunlit park background"></div>
  <div class="abs hero-swoosh" role="img" aria-label="Decorative teal and gold wave swoosh along the bottom of the header"></div>
  <div class="abs brand">Bright Path Notes</div>
  <nav class="abs nav"><span>Home</span><span>About Elena</span><span>Contact Us</span></nav>
  <div class="abs search">Search
    <svg width="10" height="10" viewBox="0 0 10 10"><circle cx="4" cy="4" r="3" fill="none" stroke="#444" stroke-width="1.5"/><line x1="6.3" y1="6.3" x2="9.3" y2="9.3" stroke="#444" stroke-width="1.5"/></svg>
  </div>
  <div class="abs hero-copy">
    <h1>ABOUT ELENA</h1>
    <p>Sed ut perspiciatis unde omnis iste natus error sit voluptatem<br>accusantium doloremque laudantium, totam rem aperiam,<br>eaque ipsa quae ab illo inventore veritatis</p>
    <span class="btn">Read More
      <svg width="11" height="11" viewBox="0 0 11 11"><circle cx="5.5" cy="5.5" r="5.5" fill="#fff"/><path d="M4.3 3 L6.8 5.5 L4.3 8" fill="none" stroke="var(--teal)" stroke-width="1.6"/></svg>
    </span>
  </div>
  <div class="abs dots"><i class="on"></i><i></i><i></i><i></i></div>
</header>

<main>
  <article class="abs post" style="top:659px">
    <div class="pic" role="img" aria-label="Two hikers with backpacks on a rocky summit above a wide valley" style="background:linear-gradient(180deg,#4f95d6 0%,#9cc7ea 45%,#5d7a58 70%,#3e3a34 100%)"></div>
    <div class="txt">
      <h2>Nemo enim ipsam voluptatem quia voluptas sit aspernatur aut odit aut fugit</h2>
      <div class="meta"><span>▦ March 25, 2017</span><span>◌ 2 comments</span><span>✎ by Jonah</span></div>
      <p class="excerpt">Lorem ipsum dolor sit amet, consectetur adipiscing elit, sed do eiusmod tempor incididunt ut labore et dolore magna aliqua. Ut enim ad minim veniam, quis nostrud exercitation ullamco laboris nisi ut aliquip ex ea commodo</p>
      <div class="share">Share : <i></i><i></i><i></i></div>
    </div>
  </article>

  <article class="abs post" style="top:942px">
    <div class="pic" role="img" aria-label="Sunset over calm water with birds flying and reeds in the foreground" style="background:linear-gradient(180deg,#5f7fa0 0%,#e39a3c 40%,#f4c65a 52%,#c98a4a 70%,#3f4650 100%)"></div>
    <div class="txt">
      <h2>Nemo enim ipsam voluptatem quia voluptas sit aspernatur aut odit aut fugit</h2>
      <div class="meta"><span>▦ March 25, 2017</span><span>◌ 2 comments</span><span>✎ by Jonah</span></div>
      <p class="excerpt">Lorem ipsum dolor sit amet, consectetur adipiscing elit, sed do eiusmod tempor incididunt ut labore et dolore magna aliqua. Ut enim ad minim veniam, quis nostrud exercitation ullamco laboris nisi ut aliquip ex ea commodo</p>
      <div class="share">Share : <i></i><i></i><i></i></div>
    </div>
  </article>

  <article class="abs post" style="top:1225px">
    <div class="pic" role="img" aria-label="Woman in a cream dress and tall brown boots lounging on a vintage sofa" style="background:linear-gradient(135deg,#4a3a2c 0%,#8a6a4c 40%,#c9b59a 60%,#5a3a26 100%)"></div>
    <div class="txt">
      <h2>Nemo enim ipsam voluptatem quia voluptas sit aspernatur aut odit aut fugit</h2>
      <div class="meta"><span>▦ March 25, 2017</span><span>◌ 2 comments</span><span>✎ by Jonah</span></div>
      <p class="excerpt">Lorem ipsum dolor sit amet, consectetur adipiscing elit, sed do eiusmod tempor incididunt ut labore et dolore magna aliqua. Ut enim ad minim veniam, quis nostrud exercitation ullamco laboris nisi ut aliquip ex ea commodo</p>
      <div class="share">Share : <i></i><i></i><i></i></div>
    </div>
  </article>

  <article class="abs post" style="top:1508px">
    <div class="pic" role="img" aria-label="Tropical bay with turquoise water, mountains and palm trees" style="background:linear-gradient(180deg,#6aa3d8 0%,#8fb9c9 30%,#1fb3c4 50%,#3f8a4a 75%,#2f5a2c 100%)"></div>
    <div class="txt">
      <h2>Nemo enim ipsam voluptatem quia voluptas sit aspernatur aut odit aut fugit</h2>
      <div class="meta"><span>▦ March 25, 2017</span><span>◌ 2 comments</span><span>✎ by Jonah</span></div>
      <p class="excerpt">Lorem ipsum dolor sit amet, consectetur adipiscing elit, sed do eiusmod tempor incididunt ut labore et dolore magna aliqua. Ut enim ad minim veniam, quis nostrud exercitation ullamco laboris nisi ut aliquip ex ea commodo</p>
      <div class="share-btns">
        <span><b>Share</b></span>
        <span><b>Post</b><em>250</em></span>
        <span><b>Share</b><em>7</em></span>
        <span><b>Share</b><em>1.3K</em></span>
      </div>
    </div>
  </article>

  <div class="abs pager"><span class="on">1</span><span>2</span><span>3</span>……<span>10</span><span class="on">»</span></div>
</main>

<aside>
  <div class="abs profile">
    <div class="band"></div>
    <div class="avatar" role="img" aria-label="Portrait of Elena, the blog author"></div>
    <h3>ELENA</h3>
    <p>Lorem ipsum dolor sit amet, consectetur adipiscing elit, sed do eiusmod tempor incididunt ut labore et dolore magna aliqua. Ut enim ad minim veniam, quis nostrud  Lorem</p>
    <div class="stars">★★★<s>★★</s></div>
  </div>

  <div class="abs side-title">REVIEWS</div>

  <div class="abs review" style="top:1044px">
    <div class="pic" role="img" aria-label="Cyclist resting beside a mountain bike on a forest trail" style="background:linear-gradient(160deg,#9aa855,#5d6b34)"></div>
    <div class="body"><h4>Nemo enim ipsam</h4><div class="stars">★★★<s>★★</s></div><p>Lorem ipsum dolor sit amet, consectetur adipiscing elit,</p><div class="by">👤 Corvel</div></div>
  </div>
  <div class="abs review" style="top:1198px">
    <div class="pic" role="img" aria-label="Hikers climbing over rocks in a green valley" style="background:linear-gradient(160deg,#6f8a6a,#3f4a3a)"></div>
    <div class="body"><h4>Nemo enim ipsam</h4><div class="stars">★★★<s>★★</s></div><p>Lorem ipsum dolor sit amet, consectetur adipiscing elit,</p><div class="by">👤 Corvel</div></div>
  </div>
  <div class="abs review" style="top:1352px">
    <div class="pic" role="img" aria-label="Smiling older man in a denim shirt" style="background:linear-gradient(160deg,#8a7866,#3d4a5c)"></div>
    <div class="body"><h4>Nemo enim ipsam</h4><div class="stars">★★★<s>★★</s></div><p>Lorem ipsum dolor sit amet, consectetur adipiscing elit,</p><div class="by">👤 Corvel</div></div>
  </div>

  <div class="abs promo" role="img" aria-label="Advertisement showing a woman running on a road with a sneaker in the foreground"></div>
</aside>

<section class="abs strip" aria-label="Photo feed">
  <div role="img" aria-label="Couple sitting on a wooden dock by a lake" style="width:171px;background:linear-gradient(160deg,#c9b98a,#6f6a4e)"></div>
  <div role="img" aria-label="Person meditating on green grass" style="width:215px;background:linear-gradient(160deg,#eaf0d8,#7fae3c)"></div>
  <div role="img" aria-label="Cyclist riding on an autumn road" style="width:215px;background:linear-gradient(160deg,#c98f3a,#8a8a80)"></div>
  <div role="img" aria-label="Woman sitting on steps in a park" style="width:215px;background:linear-gradient(160deg,#8fbf4f,#4a5a3a)"></div>
  <div role="img" aria-label="Person by a campfire in a forest" style="width:215px;background:linear-gradient(160deg,#6b5a3a,#c9a07a)"></div>
  <div role="img" aria-label="Woman with arms outstretched facing mountains" style="width:169px;background:linear-gradient(180deg,#9aa6a8,#6f8a4a)"></div>
</section>
<div class="abs follow">FOLLOW SNAPLINE <i></i></div>

<footer class="abs footer">
  <div class="f-icons"><i></i><i></i><i></i><i></i><i></i></div>
  <div class="f-nav">Home &nbsp;/&nbsp; Contact &nbsp;/&nbsp; Topics &nbsp;/&nbsp; About Elena &nbsp;/&nbsp; Discussion &nbsp;/&nbsp; Videos Links</div>
  <div class="f-copy">Copyright @ 2017 Bright Path Notes. All Rights Reserved.</div>
</footer>

</body>
</html>
```